Brivora Distance Learning Website

Brivora provide e-learning and mixed learning solutions for individuals, colleges, organisations and B2B.
We need a modern, light and flat website design for Brivora. We want to to see the designer incorporate user experience(UX) design elements into the AI or PSD mockups. We would like to see designs that use pastel colors that compliment yellow and black of our logo.
We want our E-learning experience to accelerate learning and for the interface to be user friendly and intuitive. We want the designs to focus on quick access to course information, course reviews, learning progress and study advice. Quick and intuitive access to all content for our clients is one of our top priorities.
We would like designs for the following project 3 pages:
1. Learner homepage dashboard (see attached screenshot).
On this page the Learners need to:
- Login
- Have quick access to Packages and Courses.
- See other recommended courses (Below Packages and Courses)
- Possibly a left hand side column/menu with thumbnail icons (See lumeqa learner dashboard screenshot)
2. Homepage
See current sample
http://www.brivora-learn.example
We would like the designer to focus on creating a customized banner to enhance the home page.
3. Primary Landing/Marketing page
This page is geared towards customer acquisition with the focal point being the top banner (video or HD image).
And Course Preview content below.
See reference
http://brivora-learn.example/subscriptionPlans/marketing/MTc%3D/Mjc4Nw%3D%3D/Speaking%20Nepali%20%2B%20Nepali%20Snacks%20Bundle%20by%20Lorne%20Pike%20Vell
Other site we like:
- https://www.skillorva.example (We like the home page and top bar on courses page)
- http://www.tutorcrest.example
- http://pixelgrovelab.example (think this site looks great, love the lower graphics on the homepage)
Updates
Hello,
Thank you for taking the time to contribute to this web design competition. We would just like to point out a few things:
1. Please try to make the color palette similar to the colors used in the screenshot that we just uploaded ('possible color palette).
2. Please make the designs specific to each page: THE LEARNER HOMEPAGE, HOME PAGE, and the MARKETING LANDING PAGE.
We are very happy with the high quality of designs so far,
Cheers,
Ned Ru
VK-Studio
Also,
Please avoid using dark/bold elements in the designs. The ONLY elements that we want to be dark are the logo and the footer.
Any questions please ask,
Cheers,
Ned Ru
Vk-Studio
Hello,
Based on the round of feedback we just gave it would be great if you could complete further design changes by tomorrow, as we are pushed for time.
Thank you,
Ned Ru
VK-Studio

```html
<!DOCTYPE html>
<html lang="en">
<head>
<meta charset="utf-8">
<title>Brivora – Learner Dashboard</title>
<link rel="stylesheet" href="https://fonts.googleapis.com/css2?family=Arimo:wght@400;700&family=Open+Sans:wght@400;600;700&family=Signika:wght@300;400;600&display=swap">
<style>
:root{
  --side:#4a4a4a;
  --side-top:#575757;
  --side-active:#3d3d3d;
  --accent:#f5b400;
  --badge-red:#e2493b;
  --badge-grey:#8e8e8e;
  --text:#555;
  --muted:#999;
  --line:#e2e2e2;
  --panel:#e6e6e6;
  --panel-soft:#eaeaea;
  --blue:#66b0e3;
  --blue-deep:#5b8fc9;
  --teal:#1abc9c;
  --price:#3a8ee0;
  --white:#fff;
}
*{box-sizing:border-box;margin:0;padding:0}
html,body{width:881px;height:1200px;overflow:hidden;background:var(--white)}
body{position:relative;font-family:"Open Sans",Arial,sans-serif;color:var(--text)}
.abs{position:absolute}

/* sidebar */
.sidebar{position:absolute;left:0;top:0;width:209px;height:1200px;background:var(--side)}
.sidebar-top{height:58px;background:var(--side-top);position:relative}
.menu-hex{position:absolute;left:16px;top:13px}
.nav-active{position:relative;background:var(--side-active);height:117px;border-left:5px solid var(--accent);padding:24px 0 0 17px}
.nav-item{display:flex;align-items:center;font-family:"Signika",sans-serif;font-size:9.5px;color:#d8d8d8;letter-spacing:.4px;white-space:nowrap}
.nav-item svg{margin-right:10px}
.nav-sub{font-size:7px;color:#cfcfcf;margin:8px 0 0 28px;line-height:18px}
.badge{position:absolute;right:18px;width:13px;height:13px;border-radius:50%;font-size:6.5px;color:#fff;display:flex;align-items:center;justify-content:center}
.badge-red{background:var(--badge-red)}
.badge-grey{background:var(--badge-grey)}
.nav-list{position:relative}
.nav-list .nav-item{position:absolute;left:22px;color:#cfcfcf}

/* header */
.topbar{position:absolute;left:209px;top:0;width:672px;height:58px;border-bottom:1px solid var(--line)}
.brand{position:absolute;left:20px;top:17px;display:flex;align-items:center}
.brand-dot{width:18px;height:18px;border-radius:50%;background:var(--accent);margin-right:4px}
.brand-name{font-family:"Signika",sans-serif;font-size:19px;font-weight:600;color:#222;line-height:20px}
.search{position:absolute;left:122px;top:18px;width:202px;height:26px;border:3px solid #e3e3e3;border-radius:2px;display:flex;align-items:center;padding-left:8px;font-size:6px;font-style:italic;color:#aaa}
.search svg{margin-right:6px}
.top-link{position:absolute;top:27px;font-size:8px;color:#888}
.notif-badge{position:absolute;left:539px;top:24px;width:8px;height:8px;border-radius:50%;background:var(--badge-red);font-size:5px;color:#fff;text-align:center;line-height:8px}
.avatar-small{position:absolute;left:564px;top:22px;width:18px;height:18px;border-radius:50%;background:linear-gradient(#b08a74,#6e5244)}
.user-name{position:absolute;left:588px;top:27px;font-size:8px;color:#777}

/* tiles */
.tiles{position:absolute;left:221px;top:76px;width:644px;height:107px;display:flex}
.tile{flex:1;display:flex;flex-direction:column;align-items:center;justify-content:flex-start;padding-top:20px;color:#fff;font-family:"Signika",sans-serif;font-size:9px;text-align:center;line-height:10px;letter-spacing:.3px}
.tile svg{height:34px;margin-bottom:14px}
.tile-store{background:#aaa}
.tile-subscribed{background:#9d9d9d}
.tile-published{background:#acacac}
.tile-bookmarks{background:#b6b6b6}
.tile-rewards{background:#c4c4c4}
.tile-logout{background:#d3d3d3}

/* profile */
.profile-cover{position:absolute;left:221px;top:195px;width:313px;height:185px;background:linear-gradient(135deg,#5f6a73 0%,#8c8377 45%,#b9a98f 70%,#7d6d5c 100%)}
.profile-name{position:absolute;left:221px;top:221px;width:313px;padding-left:119px;font-family:"Signika",sans-serif;font-weight:300;font-size:13px;color:#fff}
.profile-bio{position:absolute;left:255px;top:252px;width:250px;font-size:8px;color:#fff;text-align:center;line-height:13px}
.plus-box{position:absolute;width:19px;height:19px;background:var(--accent);display:flex;align-items:center;justify-content:center}
.profile-avatar{position:absolute;left:329px;top:315px}
.stat{position:absolute;top:427px;text-align:center;font-family:"Signika",sans-serif;font-weight:300;font-size:13px;color:#555;line-height:20px}

/* panels */
.panel-head{position:absolute;background:var(--panel);font-size:8px;color:#666;display:flex;align-items:center;padding-left:13px}
.pkg-item{position:absolute;left:566px;width:285px;height:31px;background:var(--panel-soft);display:flex;align-items:center;padding-left:11px;font-size:9px;color:#555;white-space:nowrap}
.check{width:13px;height:13px;background:var(--accent);display:inline-flex;align-items:center;justify-content:center;margin-right:12px;flex:none}
.check-grey{background:#a9a9a9}
.note-box{position:absolute;left:566px;top:318px;width:285px;height:99px;background:#e3e3e3;padding:10px 13px;font-size:7px;color:#999}
.btn-note{position:absolute;left:774px;top:434px;width:77px;height:26px;background:#a9a49c;color:#fff;font-size:8px;display:flex;align-items:center;justify-content:center}

/* todo */
.todo-input{position:absolute;left:671px;top:517px;width:175px;height:23px;background:var(--panel-soft)}
.todo{position:absolute;left:671px;display:flex;align-items:center;font-size:6px;color:#777}
.todo .box{width:13px;height:13px;border:1px solid #ddd;margin-right:13px;display:flex;align-items:center;justify-content:center}
.todo .box.done{background:var(--accent);border-color:var(--accent)}

.donut-label{position:absolute;top:823px;font-size:7px;color:#aaa;text-align:center;width:80px}
.files-btn{position:absolute;left:658px;top:862px;width:202px;height:45px;background:#b0aca6;color:#fff;font-family:"Signika",sans-serif;font-size:11px;display:flex;align-items:center;justify-content:space-between;padding:0 14px}

/* cards */
.card{position:absolute;top:932px;width:149px;height:197px;border:1px solid #c8c8c8;border-radius:3px;overflow:hidden;background:#fff}
.card-media{height:87px;display:flex;align-items:center;justify-content:center;position:relative}
.card-add{position:absolute;right:6px;top:6px;width:13px;height:13px;background:#bdbdbd;border:1px solid #eee;display:flex;align-items:center;justify-content:center}
.card-title{position:absolute;left:6px;top:97px;width:140px;font-family:"Arimo",Arial,sans-serif;font-weight:700;font-size:8px;color:#555;line-height:12px}
.card-author{position:absolute;left:6px;top:134px;font-size:7.5px;color:#555}
.card-date{position:absolute;left:6px;top:160px;font-size:6.5px;color:#666}
.card-foot{position:absolute;left:0;right:0;bottom:0;height:25px;border-top:1px solid #ddd;display:flex;align-items:center;padding:0 4px;font-size:7px;color:#555}
.card-foot svg{margin-right:3px}
.card-foot .rating{margin-left:9px;display:flex;align-items:center}
.card-foot .rating-center{margin-left:56px;display:flex;align-items:center}
.price{margin-left:auto;font-family:"Signika",sans-serif;font-weight:600;font-size:17px;color:var(--price)}
.pager{position:absolute;left:524px;top:1164px;display:flex;gap:4px}
</style>
</head>
<body>

<aside class="sidebar">
  <div class="sidebar-top">
    <svg class="menu-hex" width="29" height="32" viewBox="0 0 29 32"><polygon points="14.5,0 29,8 29,24 14.5,32 0,24 0,8" fill="#999"/><rect x="8" y="11" width="13" height="1.8" fill="#fff"/><rect x="8" y="15" width="13" height="1.8" fill="#fff"/><rect x="8" y="19" width="13" height="1.8" fill="#fff"/></svg>
  </div>
  <nav>
    <div class="nav-active">
      <div class="nav-item"><svg width="11" height="10" viewBox="0 0 11 10"><path d="M5.5 0L0 5h1.5v5h3V7h2v3h3V5H11z" fill="#ccc"/></svg>Dashboard</div>
      <span class="badge badge-red" style="top:24px">16</span>
      <div class="nav-sub">Learning Publisher Dashboard<br>General settings<br>Help</div>
    </div>
    <div class="nav-list">
      <div class="nav-item" style="top:15px"><svg width="12" height="10" viewBox="0 0 12 10"><rect x=".5" y=".5" width="11" height="9" fill="none" stroke="#bbb"/><rect x=".5" y=".5" width="11" height="2" fill="#bbb"/></svg>Find Learning Packages</div>
      <span class="badge badge-grey" style="top:15px">95</span>
      <div class="nav-item" style="top:54px"><svg width="12" height="10" viewBox="0 0 12 10"><rect x=".5" y=".5" width="8" height="6" fill="none" stroke="#bbb"/><rect x="3.5" y="3.5" width="8" height="6" fill="none" stroke="#bbb"/></svg>Reviews and Coments</div>
      <span class="badge badge-grey" style="top:54px">7</span>
      <div class="nav-item" style="top:93px"><svg width="12" height="11" viewBox="0 0 12 11"><circle cx="5.5" cy="5.5" r="5" fill="none" stroke="#bbb"/><path d="M5.5 5.5V.5A5 5 0 0 1 10.5 5.5z" fill="#bbb"/></svg>Purchase History</div>
      <span class="badge badge-grey" style="top:93px">7</span>
      <div class="nav-item" style="top:132px"><svg width="12" height="10" viewBox="0 0 12 10"><path d="M.5 0v9.5H12" fill="none" stroke="#bbb"/><path d="M2 8l3-4 2 2 4-5" fill="none" stroke="#bbb"/></svg>Statistic Charts</div>
      <span class="badge badge-grey" style="top:132px">6</span>
    </div>
  </nav>
</aside>

<header class="topbar">
  <div class="brand"><span class="brand-dot"></span><span class="brand-name">Brivora</span></div>
  <div class="search"><svg width="7" height="7" viewBox="0 0 7 7"><circle cx="3" cy="3" r="2.3" fill="none" stroke="#999"/><path d="M4.7 4.7L6.8 6.8" stroke="#999"/></svg>Search for courses</div>
  <span class="top-link" style="left:440px">Activity</span>
  <span class="top-link" style="left:490px">Notifications</span>
  <span class="notif-badge">15</span>
  <span class="avatar-small" role="img" aria-label="User avatar"></span>
  <span class="user-name">Dorian Velasco &#9662;</span>
</header>

<section class="tiles">
  <div class="tile tile-store"><svg viewBox="0 0 40 34" width="40"><path d="M6 12h28l-3 20H9z" fill="none" stroke="#fff" stroke-width="2.5"/><path d="M12 12L16 3M28 12L24 3" stroke="#fff" stroke-width="2"/><path d="M15 17v10M20 17v10M25 17v10" stroke="#fff" stroke-width="2"/><rect x="3" y="10" width="34" height="4" fill="#fff"/></svg>Store</div>
  <div class="tile tile-subscribed"><svg viewBox="0 0 36 34" width="36"><path d="M2 6h12l3 3h13v22H2z" fill="none" stroke="#fff" stroke-width="2.5"/><path d="M26 33l-7-7a4 4 0 0 1 7-5a4 4 0 0 1 7 5z" fill="#fff"/></svg>Subscribed<br>Learning Packages</div>
  <div class="tile tile-published"><svg viewBox="0 0 36 34" width="36"><rect x="2" y="6" width="26" height="26" fill="none" stroke="#fff" stroke-width="2.5"/><path d="M7 14h16M7 20h16M7 26h10" stroke="#fff" stroke-width="2"/><path d="M33 1l2 2-14 16-3 1 1-3z" fill="#fff"/></svg>My<br>Published Packages</div>
  <div class="tile tile-bookmarks"><svg viewBox="0 0 34 34" width="34"><polygon points="17,1 21.5,12 33,12.5 24,20 27,32 17,25.5 7,32 10,20 1,12.5 12.5,12" fill="#fff"/></svg>Bookmarks</div>
  <div class="tile tile-rewards"><svg viewBox="0 0 40 34" width="40"><path d="M9 2h22l7 10-18 20L2 12z" fill="none" stroke="#fff" stroke-width="2"/><path d="M2 12h36M14 2l-3 10 9 20 9-20-3-10M20 2l-6 10M20 2l6 10" fill="none" stroke="#fff" stroke-width="1.5"/></svg>My bRewards</div>
  <div class="tile tile-logout"><svg viewBox="0 0 34 34" width="34"><path d="M20 3H5v28h15" fill="none" stroke="#fff" stroke-width="2.5"/><path d="M13 17h19M25 10l7 7-7 7" fill="none" stroke="#fff" stroke-width="2.5"/></svg>Logout account</div>
</section>

<div class="profile-cover" role="img" aria-label="Cover photo of a laptop with code and an open book on a desk"></div>
<div class="profile-name">Marcus Ellery</div>
<p class="profile-bio">Cras et neque vel nunc aliquet dictum vitae eget velit. Maecenas lobortis leo eu odio viverra pulvinar.</p>
<div class="plus-box" style="left:501px;top:205px"><svg width="9" height="9"><path d="M4.5 0v9M0 4.5h9" stroke="#fff" stroke-width="1.6"/></svg></div>
<svg class="profile-avatar" width="88" height="96" viewBox="0 0 88 96" role="img" aria-label="Profile photo of the learner"><polygon points="44,0 88,24 88,72 44,96 0,72 0,24" fill="#fff"/><polygon points="44,5 83,27 83,69 44,91 5,69 5,27" fill="#b7aca4"/></svg>
<div class="stat" style="left:272px">Attended<br>17</div>
<div class="stat" style="left:355px">Attending<br>3</div>
<div class="stat" style="left:440px">Notes<br>260</div>

<div class="panel-head" style="left:551px;top:195px;width:314px;height:33px">Courses in Package</div>
<div class="pkg-item" style="top:239px"><span class="check"><svg width="8" height="7"><path d="M1 3.5l2 2 4-4.5" fill="none" stroke="#fff" stroke-width="1.5"/></svg></span>Speaking Nepali + Nepali Snacks Bunle By &nbsp;Lorne Pike Vell</div>
<div class="pkg-item" style="top:276px;font-size:7px;color:#888"><span class="check check-grey"><svg width="7" height="7"><path d="M3.5 0v7M0 3.5h7" stroke="#fff" stroke-width="1.4"/></svg></span>Add More Packages</div>
<div class="note-box">Your note here</div>
<div class="btn-note">Add Note</div>

<div class="panel-head" style="left:221px;top:475px;width:423px;height:33px">Quick statistics</div>
<svg class="abs" style="left:225px;top:512px" width="420" height="182" viewBox="225 512 420 182" font-family="Open Sans, sans-serif">
  <rect x="529" y="515" width="12" height="5" fill="#66b0e3"/><text x="547" y="521" font-size="6.5" fill="#888">ipsum dolor sit amet</text>
  <rect x="529" y="526" width="12" height="5" fill="#f5b400"/><text x="547" y="532" font-size="6.5" fill="#888">consectetur adipiscing elit</text>
  <g stroke="#ececec" stroke-width="1">
    <path d="M262 549H628M262 571H628M262 593H628M262 615H628M262 637H628M262 659H628M262 681H628"/>
    <path d="M273 549V681M295 549V681M318 549V681M340 549V681M363 549V681M385 549V681M408 549V681M430 549V681M452 549V681M474 549V681M496 549V681M518 549V681M541 549V681M563 549V681M586 549V681M608 549V681M628 549V681"/>
  </g>
  <g font-size="7" fill="#555" text-anchor="end">
    <text x="258" y="552">300</text><text x="258" y="574">250</text><text x="258" y="596">200</text><text x="258" y="618">150</text><text x="258" y="640">100</text><text x="258" y="662">50</text><text x="258" y="684">0</text>
  </g>
  <g font-size="7" fill="#555" text-anchor="middle">
    <text x="295" y="688">1</text><text x="340" y="688">2</text><text x="385" y="688">3</text><text x="430" y="688">4</text><text x="474" y="688">5</text><text x="518" y="688">6</text><text x="563" y="688">7</text><text x="608" y="688">8</text>
  </g>
  <polyline points="268,599 352,624 423,585 495,608 562,584 624,575" fill="none" stroke="#66b0e3" stroke-width="2"/>
  <g fill="#66b0e3" stroke="#fff" stroke-width="1.5"><circle cx="268" cy="599" r="4.5"/><circle cx="352" cy="624" r="4.5"/><circle cx="423" cy="585" r="4.5"/><circle cx="495" cy="608" r="4.5"/><circle cx="562" cy="584" r="4.5"/><circle cx="624" cy="575" r="4.5"/></g>
  <polyline points="268,667 331,653 392,659 471,637 516,626 543,574 603,561 624,551" fill="none" stroke="#f5b400" stroke-width="2"/>
  <g fill="#f5b400" stroke="#fff" stroke-width="1.5"><circle cx="268" cy="667" r="4.5"/><circle cx="331" cy="653" r="4.5"/><circle cx="392" cy="659" r="4.5"/><circle cx="471" cy="637" r="4.5"/><circle cx="516" cy="626" r="4.5"/><circle cx="543" cy="574" r="4.5"/><circle cx="603" cy="561" r="4.5"/><circle cx="624" cy="551" r="4.5"/></g>
</svg>

<svg class="abs" style="left:290px;top:752px" width="290" height="74" viewBox="290 752 290 74" font-family="Open Sans, sans-serif" font-size="13" fill="#999" text-anchor="middle">
  <g fill="none" stroke-width="4">
    <circle cx="326" cy="789" r="30" stroke="#e8e8e8"/><circle cx="326" cy="789" r="30" stroke="#66b0e3" stroke-dasharray="160 189" transform="rotate(-90 326 789)"/>
    <circle cx="434" cy="789" r="30" stroke="#e8e8e8"/><circle cx="434" cy="789" r="30" stroke="#f5b400" stroke-dasharray="122 189" transform="rotate(-90 434 789)"/>
    <circle cx="541" cy="789" r="30" stroke="#e8e8e8"/><circle cx="541" cy="789" r="30" stroke="#1ab99a" stroke-dasharray="151 189" transform="rotate(-90 541 789)"/>
  </g>
  <text x="326" y="794">85%</text><text x="434" y="794">65%</text><text x="541" y="794">80%</text>
</svg>
<div class="donut-label" style="left:289px">Web design</div>
<div class="donut-label" style="left:394px">Branding design</div>
<div class="donut-label" style="left:501px">Time management</div>

<div class="panel-head" style="left:658px;top:476px;width:202px;height:31px;padding-left:45px">Course Tracker - Todo list</div>
<div class="plus-box" style="left:670px;top:482px"><svg width="9" height="9"><path d="M4.5 0v9M0 4.5h9" stroke="#fff" stroke-width="1.6"/></svg></div>
<div class="todo-input"></div>
<div class="todo" style="top:552px"><span class="box done"><svg width="8" height="7"><path d="M1 3.5l2 2 4-4.5" fill="none" stroke="#fff" stroke-width="1.5"/></svg></span>Aliquam metus neque</div>
<div class="todo" style="top:572px"><span class="box"></span>In ut turpis non ipsum rhoncus porttitor</div>
<div class="todo" style="top:591px"><span class="box"></span>Maecenas interdum dignissim</div>
<div class="todo" style="top:611px"><span class="box"></span>Pellentesque sodales ipsum et enim</div>
<div class="todo" style="top:630px"><span class="box"></span>Quisque tincidunt mattis sapien</div>

<div class="panel-head" style="left:658px;top:668px;width:202px;height:32px">Cloud storage usage</div>
<svg class="abs" style="left:660px;top:725px" width="200" height="120" viewBox="660 725 200 120" font-family="Open Sans, sans-serif">
  <circle cx="766" cy="783" r="48" fill="none" stroke="#e6e6e6" stroke-width="16"/>
  <circle cx="766" cy="783" r="48" fill="none" stroke="#5aa9e2" stroke-width="16" stroke-dasharray="184 302" transform="rotate(-90 766 783)"/>
  <text x="760" y="785" font-size="15" fill="#666" text-anchor="middle">140 / 512</text>
  <text x="760" y="803" font-size="13" fill="#666" text-anchor="middle">GB</text>
  <path d="M686 782V794H706" fill="none" stroke="#ccc" stroke-width=".8"/>
  <text x="670" y="778" font-size="5.5" fill="#777">Free space</text>
  <path d="M794 741H836V766" fill="none" stroke="#aad0ee" stroke-width=".8"/>
  <text x="821" y="775" font-size="5.5" fill="#777">Storage use</text>
</svg>

<div class="files-btn">Show my files<svg width="7" height="11"><path d="M1 1l5 4.5L1 10" fill="none" stroke="#fff" stroke-width="1.5"/></svg></div>

<div class="panel-head" style="left:221px;top:874px;width:423px;height:33px">Recommended &nbsp;Packages and Courses</div>

<article class="card" style="left:224px">
  <div class="card-media" style="background:linear-gradient(180deg,#e3a23a,#d4722a 60%,#6a4326)" role="img" aria-label="Temple silhouette at sunset">
    <span class="card-add"><svg width="7" height="7"><path d="M3.5 0v7M0 3.5h7" stroke="#fff" stroke-width="1.3"/></svg></span>
  </div>
  <div class="card-title">Cras scelerisque et ante eget lacinia iaculis ullamcorper augue.</div>
  <div class="card-author">Mr Alan Birch</div>
  <div class="card-date">12th August 2013</div>
  <div class="card-foot"><svg width="11" height="7"><ellipse cx="5.5" cy="3.5" rx="5.3" ry="3.3" fill="#555"/><circle cx="5.5" cy="3.5" r="1.6" fill="#fff"/></svg>102<span class="rating"><svg width="9" height="9" viewBox="0 0 34 34"><polygon points="17,1 21.5,12 33,12.5 24,20 27,32 17,25.5 7,32 10,20 1,12.5 12.5,12" fill="#555"/></svg>&nbsp;4.6</span><span class="price">50$</span></div>
</article>

<article class="card" style="left:386px">
  <div class="card-media" style="background:var(--teal)">
    <span class="card-add"><svg width="7" height="7"><path d="M3.5 0v7M0 3.5h7" stroke="#fff" stroke-width="1.3"/></svg></span>
    <svg width="56" height="26" viewBox="0 0 56 26"><path d="M2 9h12M6 14h8M0 19h14" stroke="#fff" stroke-width="2"/><rect x="18" y="3" width="36" height="21" fill="#fff"/><path d="M18 3l18 12 18-12" fill="none" stroke="#1abc9c" stroke-width="2"/></svg>
  </div>
  <div class="card-title">Cras scelerisque et ante eget lacinia iaculis ullamcorper augue.</div>
  <div class="card-author">Mr Alan Birch</div>
  <div class="card-date">12th August 2013</div>
  <div class="card-foot"><svg width="11" height="7"><ellipse cx="5.5" cy="3.5" rx="5.3" ry="3.3" fill="#555"/><circle cx="5.5" cy="3.5" r="1.6" fill="#fff"/></svg>102<span class="rating"><svg width="9" height="9" viewBox="0 0 34 34"><polygon points="17,1 21.5,12 33,12.5 24,20 27,32 17,25.5 7,32 10,20 1,12.5 12.5,12" fill="#555"/></svg>&nbsp;4.6</span><span class="price">75$</span></div>
</article>

<article class="card" style="left:549px">
  <div class="card-media" style="background:var(--blue-deep)">
    <span class="card-add"><svg width="7" height="7"><path d="M3.5 0v7M0 3.5h7" stroke="#fff" stroke-width="1.3"/></svg></span>
    <svg width="30" height="34" viewBox="0 0 30 34"><path d="M10 1h10M12 1v11L2 31h26L18 12V1" fill="#fff" stroke="#fff" stroke-width="2" stroke-linejoin="round"/><circle cx="12" cy="24" r="2" fill="#5b8fc9"/><circle cx="18" cy="20" r="1.5" fill="#5b8fc9"/><circle cx="18" cy="27" r="1.5" fill="#5b8fc9"/></svg>
  </div>
  <div class="card-title">Cras scelerisque et ante eget lacinia iaculis ullamcorper augue.</div>
  <div class="card-author">Mr Alan Birch</div>
  <div class="card-date">12th August 2013</div>
  <div class="card-foot"><svg width="11" height="7"><ellipse cx="5.5" cy="3.5" rx="5.3" ry="3.3" fill="#555"/><circle cx="5.5" cy="3.5" r="1.6" fill="#fff"/></svg>102<span class="rating"><svg width="9" height="9" viewBox="0 0 34 34"><polygon points="17,1 21.5,12 33,12.5 24,20 27,32 17,25.5 7,32 10,20 1,12.5 12.5,12" fill="#555"/></svg>&nbsp;3.6</span><span class="price">75$</span></div>
</article>

<article class="card" style="left:713px">
  <div class="card-media" style="background:#6cb4e4">
    <span class="card-add"><svg width="7" height="7"><path d="M3.5 0v7M0 3.5h7" stroke="#fff" stroke-width="1.3"/></svg></span>
    <svg width="36" height="32" viewBox="0 0 36 32"><rect x="5" y="13" width="4" height="13" fill="#fff"/><rect x="11" y="8" width="4" height="18" fill="#fff"/><rect x="17" y="15" width="4" height="11" fill="#fff"/><rect x="23" y="4" width="4" height="22" fill="#fff"/><rect x="0" y="28" width="36" height="3" fill="#fff"/></svg>
  </div>
  <div class="card-title">Cras scelerisque et ante eget lacinia iaculis ullamcorper augue.</div>
  <div class="card-author">Mr Alan Birch</div>
  <div class="card-date">12th August 2013</div>
  <div class="card-foot"><span class="rating-center">3.6&nbsp;<svg width="9" height="9" viewBox="0 0 34 34"><polygon points="17,1 21.5,12 33,12.5 24,20 27,32 17,25.5 7,32 10,20 1,12.5 12.5,12" fill="#555"/></svg></span><span class="price">75$</span></div>
</article>

<div class="pager">
  <svg width="12" height="13" viewBox="0 0 12 13"><polygon points="6,0 12,3.25 12,9.75 6,13 0,9.75 0,3.25" fill="#999"/></svg>
  <svg width="12" height="13" viewBox="0 0 12 13"><polygon points="6,0 12,3.25 12,9.75 6,13 0,9.75 0,3.25" fill="#999"/></svg>
  <svg width="12" height="13" viewBox="0 0 12 13"><polygon points="6,0 12,3.25 12,9.75 6,13 0,9.75 0,3.25" fill="#999"/></svg>
</div>

</body>
</html>
```